business card for a massage therapy practice named 'Cedar and Willow Massage Studio'

I really need a trendy, yet easy on the eyes business card to complement my logo. Ideally with some gold or rose gold foil work.

My uploaded file of the logo I have in horizontal but I have a vertical version as well. Another color that is used in the website is a blush pink here and there. I'd like to see some trendy tropical leaves in the design.

```html
<!DOCTYPE html>
<html lang="en">
<head>
<meta charset="UTF-8">
<title>Cedar and Willow Massage Studio – Business Card</title>
<link href="https://fonts.googleapis.com/css2?family=Lato:wght@400;700&family=Dancing+Script:wght@700&display=swap" rel="stylesheet">
<style>
  :root {
    --page-bg: #e9eaea;
    --card-white: #ffffff;
    --teal-deep: #3a978c;
    --teal-mid: #17b3ad;
    --teal-bright: #4ee6e6;
    --aqua-light: #9ff2ee;
    --ink: #1f2a2a;
    --ink-soft: #4a5555;
    --name-green: #2f5e4e;
    --mint: #7fd1bf;
    --leaf-pale: #dcebc8;
    --gold: #b9a06a;
  }
  * { box-sizing: border-box; margin: 0; padding: 0; }
  html, body { width: 1200px; height: 1200px; overflow: hidden; }
  body {
    background: var(--page-bg);
    font-family: "Lato", sans-serif;
    display: flex;
    flex-direction: column;
    align-items: center;
    justify-content: center;
    gap: 56px;
  }
  .card {
    position: relative;
    width: 900px;
    height: 514px;
    overflow: hidden;
    box-shadow: 0 10px 30px rgba(0,0,0,0.15);
  }

  /* Front: contact side */
  .card-front { background: var(--card-white); }
  .card-front .wave { position: absolute; inset: 0; width: 100%; height: 100%; }
  .leaf-top {
    position: absolute; left: 250px; top: -40px; width: 320px; height: 210px;
    border-radius: 50% 50% 60% 40%;
    background: radial-gradient(ellipse at 40% 40%, #cfe5b8, var(--leaf-pale) 60%, rgba(220,235,200,0) 75%);
  }
  .leaf-corner {
    position: absolute; right: -30px; bottom: -20px; width: 220px; height: 230px;
    border-radius: 50%;
    background: radial-gradient(ellipse at 60% 60%, #d6eac2, rgba(220,235,200,0) 70%);
  }
  .person { position: absolute; left: 60px; top: 70px; }
  .person-name {
    font-family: "Dancing Script", cursive;
    font-size: 44px; color: var(--name-green); line-height: 1;
  }
  .person-title { font-size: 20px; color: var(--ink-soft); margin-top: 4px; }
  .contact-list { list-style: none; margin-top: 18px; }
  .contact-list li {
    display: flex; align-items: center; gap: 10px;
    font-size: 20px; color: var(--ink-soft); margin-bottom: 8px;
  }
  .contact-list svg { width: 16px; height: 16px; fill: var(--name-green); flex: none; }
  .brand {
    position: absolute; left: 480px; top: 210px;
    display: flex; align-items: center; gap: 16px;
  }
  .brand-dot { width: 26px; height: 26px; border-radius: 50%; background: var(--gold); }
  .brand-name { font-size: 34px; font-weight: 700; color: var(--ink); line-height: 1.15; }
  .brand-name span { display: block; }
  .address {
    position: absolute; right: 80px; bottom: 60px;
    text-align: right; font-size: 22px; color: var(--ink-soft); line-height: 1.35;
  }
  .address svg { width: 16px; height: 16px; fill: var(--teal-deep); vertical-align: middle; margin-left: 6px; }

  /* Back: brand side */
  .card-back {
    background:
      radial-gradient(circle at 70% 35%, rgba(255,255,255,0.35), rgba(255,255,255,0) 40%),
      linear-gradient(135deg, var(--teal-bright), #38d8d8 45%, var(--aqua-light));
  }
  .card-back .wave { position: absolute; inset: 0; width: 100%; height: 100%; }
  .back-brand { position: absolute; left: 150px; top: 70px; }
  .back-brand-name { font-size: 56px; font-weight: 700; color: var(--ink); line-height: 1.05; }
  .back-brand-tag { font-size: 22px; color: var(--ink); margin-top: 10px; margin-left: 60px; }
  .spa-still-life {
    position: absolute; right: 70px; bottom: 40px; width: 360px; height: 220px;
    border-radius: 40px;
    background: linear-gradient(90deg, #cfc8bd 0%, #e6e0d4 40%, #f6f7ea 65%, #e7a9d8 100%);
    opacity: 0.9;
  }
</style>
</head>
<body>

  <section class="card card-front" aria-label="Business card, contact side">
    <svg class="wave" viewBox="0 0 900 514" preserveAspectRatio="none" aria-hidden="true">
      <defs>
        <linearGradient id="frontWave" x1="0" y1="0" x2="1" y2="1">
          <stop offset="0" stop-color="#3fb8ae"/>
          <stop offset="0.5" stop-color="#19b4ad"/>
          <stop offset="1" stop-color="#3a978c"/>
        </linearGradient>
      </defs>
      <path d="M0 360 C 150 420, 250 480, 330 514 L0 514 Z" fill="url(#frontWave)"/>
      <path d="M0 330 C 140 390, 260 470, 350 514" fill="none" stroke="#ffffff" stroke-width="10"/>
      <path d="M0 318 C 140 378, 260 462, 360 514" fill="none" stroke="#3a978c" stroke-width="4"/>
    </svg>
    <div class="leaf-top" role="img" aria-label="Pale green tropical monstera and palm leaves"></div>
    <div class="leaf-corner" role="img" aria-label="Pale green palm fronds"></div>

    <div class="person">
      <p class="person-name">Mara Ellis</p>
      <p class="person-title">Director</p>
      <ul class="contact-list">
        <li><svg viewBox="0 0 24 24"><path d="M6.6 10.8a15 15 0 0 0 6.6 6.6l2.2-2.2a1 1 0 0 1 1-.25 11.4 11.4 0 0 0 3.6.57 1 1 0 0 1 1 1V20a1 1 0 0 1-1 1A17 17 0 0 1 3 4a1 1 0 0 1 1-1h3.5a1 1 0 0 1 1 1 11.4 11.4 0 0 0 .57 3.6 1 1 0 0 1-.25 1z"/></svg>1-555-014-2290</li>
        <li><svg viewBox="0 0 24 24"><path d="M2 5h20v14H2z M2 5l10 8 10-8" stroke="#2f5e4e" stroke-width="2" fill="none"/></svg>mara@cedarandwillow.com</li>
        <li><svg viewBox="0 0 24 24"><circle cx="12" cy="12" r="10"/></svg>www.cedarandwillow.com</li>
      </ul>
    </div>

    <div class="brand">
      <span class="brand-dot"></span>
      <p class="brand-name"><span>Cedar and Willow</span><span>Massage Studio</span></p>
    </div>

    <p class="address">Harbor City<svg viewBox="0 0 24 24"><path d="M12 2a7 7 0 0 0-7 7c0 5 7 13 7 13s7-8 7-13a7 7 0 0 0-7-7zm0 9.5A2.5 2.5 0 1 1 12 6.5a2.5 2.5 0 0 1 0 5z"/></svg><br>Coastal Land</p>
  </section>

  <section class="card card-back" aria-label="Business card, brand side">
    <svg class="wave" viewBox="0 0 900 514" preserveAspectRatio="none" aria-hidden="true">
      <defs>
        <linearGradient id="backWave" x1="0" y1="0" x2="1" y2="0">
          <stop offset="0" stop-color="#3a978c"/>
          <stop offset="1" stop-color="#17b3ad"/>
        </linearGradient>
      </defs>
      <path d="M0 0 L40 0 C 120 120, 200 330, 420 514 L0 514 Z" fill="url(#backWave)"/>
      <path d="M40 0 C 120 120, 200 330, 420 514" fill="none" stroke="#9ff2ee" stroke-width="3"/>
    </svg>
    <div class="back-brand">
      <p class="back-brand-name">Cedar and Willow</p>
      <p class="back-brand-tag">Massage Studio</p>
    </div>
    <div class="spa-still-life" role="img" aria-label="Stacked spa stones, frangipani flowers, a lit candle and pink bath balls"></div>
  </section>

</body>
</html>
```